Design a WordPress layout for a home loans company

The home loans company in question is going through a rebrand and needs a new website layout.
Sites they like: http://www.brightkeylending.com.au/
Current logo: Attached.
Colours to be used: As per those used in logo.
Primary: #71aa3d
Secondary: #130e10
Pages to be designed:
- Homepage
- Internal services page
Menu items for display purposes:
- Home
- About Us
- Speak to a Broker
- Articles
- Contact Us
A modern design with simplicity is key.
For copy, dummy text such as Lorem ipsum will be fine.
If you would like anything elso, please ask.
Target Market(s)
25-40 year old
Mostly female
Buying their first home in most cases
Industry/Entity Type
Mortgage Brokerage
Number of Pages Required
2 page

```html
<!DOCTYPE html>
<html lang="en">
<head>
<meta charset="utf-8">
<title>BKL Home Loans</title>
<link rel="stylesheet" href="https://fonts.googleapis.com/css2?family=Open+Sans:wght@400;600;700;800&family=Montserrat:wght@400;500&display=swap">
<style>
:root{
  --green:#71aa3d;
  --green-dark:#5f9431;
  --ink:#130e10;
  --heading:#2b2b2b;
  --text:#666;
  --dark:#262626;
  --footer:#2f2f2f;
  --line:#cfcfcf;
  --white:#fff;
}
*{box-sizing:border-box;margin:0;padding:0}
html,body{width:1200px;height:3125px;overflow:hidden}
body{font-family:"Montserrat",sans-serif;color:var(--text);background:var(--white);position:relative}
.abs{position:absolute}
h1,h2,h3{font-family:"Open Sans",sans-serif;font-weight:700}

/* top bar */
.topbar{left:0;top:0;width:1200px;height:42px}
.topbar-contact{left:530px;top:0;width:1070px;height:42px;background:var(--green);display:flex;align-items:center;gap:46px;padding-left:26px;color:var(--white);font-size:15px}
.topbar-contact span{display:flex;align-items:center;gap:12px}
.enquire{left:988px;top:0;width:135px;height:42px;background:var(--ink);color:var(--white);font:700 19px "Open Sans",sans-serif;display:flex;align-items:center;justify-content:center;letter-spacing:.5px}

/* header */
.header{left:0;top:42px;width:1200px;height:104px}
.brand{left:77px;top:70px;display:flex;align-items:center;gap:12px;font:700 34px "Open Sans",sans-serif;color:var(--green)}
.brand-mark{width:22px;height:22px;background:var(--green)}
.nav{right:70px;top:84px;display:flex;gap:40px;font-size:15px;color:#444;text-transform:uppercase}
.nav .active{color:var(--green)}

/* hero */
.hero-photo{left:0;top:146px;width:770px;height:552px;background:linear-gradient(160deg,#4f6a4a 0%,#9bb0a0 40%,#c9b7b0 65%,#7c8a66 100%)}
.hero-panel{left:770px;top:146px;width:430px;height:552px;background:var(--green)}
.hero-title{right:80px;top:318px;text-align:right;color:var(--white);font-size:48px;line-height:58px;font-weight:600}
.hero-sub{right:80px;top:454px;text-align:right;color:var(--white);font-size:15px;line-height:27px;width:240px}

/* welcome */
.welcome{left:0;top:698px;width:1200px;text-align:center}
.welcome h2{margin-top:42px;font-size:41px;color:var(--heading)}
.welcome h2 em,.green{color:var(--green);font-style:normal}
.welcome p{width:1010px;margin:22px auto 0;font-size:13.5px;line-height:27px;color:#777}
.welcome p+p{margin-top:12px}

/* features */
.features{left:0;top:1031px;width:1200px;height:469px;background:linear-gradient(180deg,#2c3030 0%,#1d2220 60%,#2e3a2a 100%)}
.features h2{position:absolute;top:44px;width:100%;text-align:center;font-size:37px;color:var(--white);font-weight:600}
.card{top:115px;width:322px;height:260px;border:1px solid rgba(255,255,255,.25);border-radius:10px;background:rgba(0,0,0,.35);padding:30px 28px;color:var(--white)}
.card-head{display:flex;align-items:center;gap:22px;height:72px}
.card-icon{width:72px;height:72px;border-radius:50%;background:rgba(255,255,255,.08);display:flex;align-items:center;justify-content:center;flex:none}
.card-head h3{font:500 19px "Montserrat",sans-serif;line-height:30px}
.card p{margin-top:26px;font-size:14px;line-height:25px;color:#e6e6e6}

/* speak */
.speak-photo{left:104px;top:1520px;width:406px;height:438px;background:linear-gradient(180deg,#efe7e2 0%,#d8c4b8 45%,#2a2a30 100%)}
.speak-ring{left:90px;top:1540px;width:420px;height:420px;border-radius:50%;border:1px solid #eee}
.speak-title{left:640px;top:1556px;font-size:41px;color:var(--heading)}
.speak-text{left:640px;top:1622px;width:480px;font-size:14px;line-height:26px;color:#777}
.field{width:219px;height:46px;border:1px solid var(--line);font-size:14px;color:#777;padding:0 12px;display:flex;align-items:center}
.submit{left:640px;top:1829px;width:154px;height:46px;background:var(--green);color:var(--white);font:700 19px "Open Sans",sans-serif;display:flex;align-items:center;justify-content:center}

/* find broker */
.find{left:0;top:1958px;width:1200px;height:313px;background:linear-gradient(180deg,#1f2424 0%,#2b3229 55%,#364330 100%)}
.find h2{position:absolute;top:60px;width:100%;text-align:center;color:var(--white);font-size:41px;font-weight:600}
.find p{position:absolute;top:123px;width:100%;text-align:center;color:var(--white);font-size:17px}
.find-input{left:308px;top:182px;width:386px;height:46px;border:1px solid rgba(255,255,255,.6);color:var(--white);font-size:14px;padding:0 18px;display:flex;align-items:center}
.find-btn{left:704px;top:182px;width:188px;height:46px;background:var(--green);color:var(--white);font:700 20px "Open Sans",sans-serif;display:flex;align-items:center;justify-content:center}

/* articles */
.articles-title{left:79px;top:2330px;font-size:41px;color:var(--heading)}
.article{left:79px;width:520px}
.article h3{font-size:19.5px;color:#333;font-weight:600}
.article-meta{display:flex;gap:48px;margin-top:14px;font-size:14px;color:#666}
.article-meta span{display:flex;align-items:center;gap:16px}
.article p{margin-top:16px;font-size:13.5px;line-height:26px;color:#777}
.article-rule{left:79px;top:2541px;width:64px;height:1px;background:#bbb}
.house-ring{left:612px;top:2290px;width:480px;height:480px;border-radius:50%;border:1px solid #eee}
.house{left:660px;top:2380px;width:530px;height:300px;background:linear-gradient(180deg,#3a3f4a 0%,#555a66 35%,#e9c07a 60%,#f4f4f4 100%)}

/* footer */
.footer{left:0;top:2771px;width:1200px;height:291px;background:var(--footer)}
.footer-brand{left:77px;top:2749px;width:312px;height:146px;background:#3c3c3c;display:flex;align-items:center;justify-content:center;gap:12px;font:700 34px "Open Sans",sans-serif;color:var(--green)}
.footer h4{position:absolute;font:700 22px "Open Sans",sans-serif;color:var(--green)}
.newsletter-input{left:77px;top:2955px;width:312px;height:46px;border:1px solid #777;color:#999;font-style:italic;font-size:14px;padding:0 18px;display:flex;align-items:center;justify-content:space-between}
.sitemap{position:absolute;font-size:14.5px;color:#e6e6e6;display:grid;grid-template-columns:163px 140px;row-gap:22px}
.sitemap span{display:flex;align-items:center;gap:14px}
.contact-list{position:absolute;left:800px;top:2878px;width:300px;font-size:14.5px;color:#e6e6e6;line-height:25px}
.contact-list div{display:flex;gap:18px;margin-bottom:18px}
.bottombar{left:0;top:3062px;width:1200px;height:63px;background:var(--green);color:var(--white);font-size:14px;display:flex;align-items:center;padding-left:79px}
.to-top{left:1075px;top:3070px;width:48px;height:48px;border:2px solid var(--white);border-radius:50%;display:flex;align-items:center;justify-content:center}
</style>
</head>
<body>

<div class="abs topbar">
  <div class="abs topbar-contact">
    <span><svg width="18" height="18" viewBox="0 0 24 24"><path fill="#fff" d="M6.6 10.8a15 15 0 0 0 6.6 6.6l2.2-2.2c.3-.3.7-.4 1-.2 1.1.4 2.3.6 3.6.6.6 0 1 .4 1 1V20c0 .6-.4 1-1 1A17 17 0 0 1 3 4c0-.6.4-1 1-1h3.5c.6 0 1 .4 1 1 0 1.3.2 2.5.6 3.6.1.3 0 .7-.2 1z"/></svg>123 456 7890</span>
    <span><svg width="20" height="16" viewBox="0 0 24 18"><rect x="1" y="1" width="22" height="16" rx="2" fill="none" stroke="#fff" stroke-width="2"/><path d="M1 2l11 8 11-8" fill="none" stroke="#fff" stroke-width="2"/></svg>info@bkl_homeloans.com</span>
  </div>
  <div class="abs enquire">ENQUIRE</div>
</div>

<div class="abs header"></div>
<div class="abs brand"><span class="brand-mark"></span>BKL Home Loans</div>
<nav class="abs nav"><span class="active">Home</span><span>About</span><span>Speak to broker</span><span>Articles</span><span>Contact</span></nav>

<div class="abs hero-photo" role="img" aria-label="Smiling couple holding a piss-bank style savings pot in front of a suburban house"></div>
<div class="abs hero-panel"></div>
<h1 class="abs hero-title">BKL HOME<br>LOANS</h1>
<p class="abs hero-sub">Lorem Ipsum is simply dummy text of the printing and typeset.</p>

<section class="abs welcome">
  <h2><em>WELCOME TO</em> BKL HOME LOANS</h2>
  <p>Lorem Ipsum is simply dummy text of the printing and typesetting industry. Lorem Ipsum has been the industry's standard dummy text ever since the 1500s, when an unknown printer took a galley of type and scrambled it to make a type specimen book. It has survived not only five centuries, but also the leap into electronic typesetting,.</p>
  <p>It has survived not only five centuries, but also the leap into electronic typesetting, remaining essentially unchanged. It was popularised in the 1960s with the release of Letraset sheets containing Lorem Ipsum passages.</p>
</section>

<section class="abs features" role="img" aria-label="Dark-toned photo of a family walking outdoors behind the feature cards">
  <h2><span class="green">With a</span> BKL HOME LOANS<span class="green">, you'll have:</span></h2>
  <div class="abs card" style="left:77px">
    <div class="card-head"><div class="card-icon"><svg width="34" height="34" viewBox="0 0 24 24" fill="none" stroke="#71aa3d" stroke-width="1.6"><circle cx="12" cy="12" r="9"/><path d="M3 12h18M12 3c3 3 3 15 0 18M12 3c-3 3-3 15 0 18"/></svg></div><h3>Local experts</h3></div>
    <p>With brokers all across Australia, you can be confident there is a professional near you with in-depth knowledge of your local area.</p>
  </div>
  <div class="abs card" style="left:438px">
    <div class="card-head"><div class="card-icon"><svg width="34" height="34" viewBox="0 0 24 24" fill="none" stroke="#71aa3d" stroke-width="1.6"><circle cx="12" cy="9" r="6"/><path d="M8.5 14l-2 8 5.5-3 5.5 3-2-8"/></svg></div><h3>Ongoing trusted advice</h3></div>
    <p>We believe in the power of advice to help you both now and into the future as your circumstances and needs change.</p>
  </div>
  <div class="abs card" style="left:800px">
    <div class="card-head"><div class="card-icon"><svg width="34" height="34" viewBox="0 0 24 24" fill="none" stroke="#71aa3d" stroke-width="1.6"><path d="M2 10h4v11H2zM6 20h11l3-8v-2h-7l1-5-2-1-6 7"/></svg></div><h3>Greater choice</h3></div>
    <p>Financial solutions aren't one-size-fits all, and our extensive range of lenders and products ensures we have the right solution.</p>
  </div>
</section>

<div class="abs speak-ring"></div>
<div class="abs speak-photo" role="img" aria-label="Confident broker in a dark suit with arms folded"></div>
<h2 class="abs speak-title"><span class="green">SPEAK TO</span> BROKER</h2>
<p class="abs speak-text">Please feel free to contact us at the information provided below and we will be sure to get back to you as soon as possible.</p>
<div class="abs field" style="left:640px;top:1704px">Name</div>
<div class="abs field" style="left:877px;top:1704px">Phone No.</div>
<div class="abs field" style="left:640px;top:1767px">Email</div>
<div class="abs field" style="left:877px;top:1767px">Subject</div>
<div class="abs submit">SUBMIT</div>

<section class="abs find" role="img" aria-label="Darkened photo of a suburban house at dusk">
  <h2>FIND A LOCAL BROKER</h2>
  <p>Lorem Ipsum is simply dummy text of the printing and typesetting industry.</p>
  <div class="abs find-input">Suburb/town or postcode</div>
  <div class="abs find-btn">FIND BROKER</div>
</section>

<h2 class="abs articles-title"><span class="green">LATEST</span> ARTICLES</h2>
<article class="abs article" style="top:2400px">
  <h3>Lorem Ipsum is simply dummy text of the printing.</h3>
  <div class="article-meta"><span><svg width="16" height="16" viewBox="0 0 24 24"><rect x="2" y="4" width="20" height="18" rx="2" fill="#71aa3d"/><rect x="5" y="10" width="14" height="9" fill="#fff"/></svg>Aug 12, 2018</span><span><svg width="18" height="18" viewBox="0 0 24 24" fill="none" stroke="#71aa3d" stroke-width="2"><path d="M4 4h10M4 4v16h16V10M10 14l10-10"/></svg>By, Name Surname</span></div>
  <p>Lorem Ipsum is simply dummy text of the printing and typesetting industry<br>Lorem Ipsum has been the industry's standard dummy text ever</p>
</article>
<div class="abs article-rule"></div>
<article class="abs article" style="top:2575px">
  <h3>Lorem Ipsum is simply dummy text of the printing.</h3>
  <div class="article-meta"><span><svg width="16" height="16" viewBox="0 0 24 24"><rect x="2" y="4" width="20" height="18" rx="2" fill="#71aa3d"/><rect x="5" y="10" width="14" height="9" fill="#fff"/></svg>Aug 12, 2018</span><span><svg width="18" height="18" viewBox="0 0 24 24" fill="none" stroke="#71aa3d" stroke-width="2"><path d="M4 4h10M4 4v16h16V10M10 14l10-10"/></svg>By, Name Surname</span></div>
  <p>Lorem Ipsum is simply dummy text of the printing and typesetting industry<br>Lorem Ipsum has been the industry's standard dummy text ever.</p>
</article>
<div class="abs house-ring"></div>
<div class="abs house" role="img" aria-label="Model of a two-storey house with dark roof and yellow walls"></div>

<footer class="abs footer">
  <h4 style="left:441px;top:52px">Sitemap</h4>
  <div class="sitemap" style="left:441px;top:105px">
    <span><svg width="14" height="14" viewBox="0 0 24 24"><circle cx="12" cy="12" r="10" fill="none" stroke="#71aa3d" stroke-width="2"/><path d="M10 7l5 5-5 5" fill="none" stroke="#71aa3d" stroke-width="2"/></svg>Home</span>
    <span><svg width="14" height="14" viewBox="0 0 24 24"><circle cx="12" cy="12" r="10" fill="none" stroke="#71aa3d" stroke-width="2"/><path d="M10 7l5 5-5 5" fill="none" stroke="#71aa3d" stroke-width="2"/></svg>Articles</span>
    <span><svg width="14" height="14" viewBox="0 0 24 24"><circle cx="12" cy="12" r="10" fill="none" stroke="#71aa3d" stroke-width="2"/><path d="M10 7l5 5-5 5" fill="none" stroke="#71aa3d" stroke-width="2"/></svg>About Us</span>
    <span><svg width="14" height="14" viewBox="0 0 24 24"><circle cx="12" cy="12" r="10" fill="none" stroke="#71aa3d" stroke-width="2"/><path d="M10 7l5 5-5 5" fill="none" stroke="#71aa3d" stroke-width="2"/></svg>Contact</span>
    <span><svg width="14" height="14" viewBox="0 0 24 24"><circle cx="12" cy="12" r="10" fill="none" stroke="#71aa3d" stroke-width="2"/><path d="M10 7l5 5-5 5" fill="none" stroke="#71aa3d" stroke-width="2"/></svg>Speak to broker</span>
  </div>
  <h4 style="left:800px;top:52px">Contact Info</h4>
  <h4 style="left:79px;top:148px">Newsletter Signup</h4>
</footer>
<div class="abs footer-brand"><span class="brand-mark"></span>BKL Home Loans</div>
<div class="abs newsletter-input">Email Address<svg width="26" height="22" viewBox="0 0 24 24"><path d="M2 21l21-9L2 3v7l15 2-15 2z" fill="#71aa3d"/></svg></div>
<div class="contact-list">
  <div><svg width="18" height="22" viewBox="0 0 24 24" style="flex:none"><path d="M12 2a7 7 0 0 0-7 7c0 5 7 13 7 13s7-8 7-13a7 7 0 0 0-7-7zm0 9.5a2.5 2.5 0 1 1 0-5 2.5 2.5 0 0 1 0 5z" fill="#71aa3d"/></svg>Lorem Ipsum is simply dummy text of the printing and typesetting industry.</div>
  <div><svg width="18" height="18" viewBox="0 0 24 24" style="flex:none"><path fill="#71aa3d" d="M6.6 10.8a15 15 0 0 0 6.6 6.6l2.2-2.2c.3-.3.7-.4 1-.2 1.1.4 2.3.6 3.6.6.6 0 1 .4 1 1V20c0 .6-.4 1-1 1A17 17 0 0 1 3 4c0-.6.4-1 1-1h3.5c.6 0 1 .4 1 1 0 1.3.2 2.5.6 3.6.1.3 0 .7-.2 1z"/></svg>123 456 7890</div>
  <div><svg width="18" height="16" viewBox="0 0 24 18" style="flex:none;margin-top:4px"><rect x="1" y="1" width="22" height="16" rx="2" fill="none" stroke="#71aa3d" stroke-width="2"/><path d="M1 2l11 8 11-8" fill="none" stroke="#71aa3d" stroke-width="2"/></svg>info@bkl_homeloans.com</div>
</div>
<div class="abs bottombar">©BKL HOME LOANS. 2018 - All Rights Reserved.</div>
<div class="abs to-top"><svg width="18" height="18" viewBox="0 0 24 24"><path d="M5 16l7-7 7 7" fill="none" stroke="#fff" stroke-width="3"/></svg></div>

</body>
</html>
```